we can communicate on this, but i want to follow the approach we took on Pellew|Marsh & Quinlan but i feel the card front needs the black background and the platinum and gold logo. The back? I am open. we can use the same info from PM&Q. Velmont Arc is an enhanced equity investment fund - basically a very exclusive boutique hedge fund that uses only stock options. very advanced things. hope you are interested

Contact Information for Business Card

Dr. Lewis T. Brennick, CFA
Scientifique de fusée financière
701.555.0143
LTBquant47@mailvantor.com

4718 Willow Creek Bend W.
West Fargo, ND 58078

No web site

Colors

Designer to choose colors to be used in the design.

Requirements
Nice to have
• I tend to prefer the most visible applications of the logo to include logo and name, the logo version with a black background and the gold and platinum components separated by the black. I see this working well for a single side (logo and name - this is card front to me).
• I am fairly open to other treatments on the reverse side with the data. To me, it makes sense to have a different color rendition of the logo on the reverse and it may be a muted black tone on tone or an oversized portion that would have spot UV. Or, the reverse may play with colors and layout
Should not have
• Other colors = no no
• Decorative font

```html
<!DOCTYPE html>
<html lang="en">
<head>
<meta charset="utf-8">
<title>Velmont Arc — Business Card</title>
<link rel="stylesheet" href="https://fonts.googleapis.com/css2?family=Montserrat:wght@400;500;600&display=swap">
<style>
  :root {
    --stage: #8e8e8e;
    --card: #2a2a2c;
    --card-deep: #1c1c1e;
    --gold: #c9a740;
    --platinum: #d8d8da;
    --paper: #ffffff;
    --ink: #1e1e20;
    --text-light: #f2f2f2;
  }
  * { box-sizing: border-box; margin: 0; padding: 0; }
  html, body {
    width: 1200px;
    height: 930px;
    overflow: hidden;
  }
  body {
    background: var(--stage);
    font-family: "Montserrat", sans-serif;
    position: relative;
  }
  .card {
    position: absolute;
    width: 520px;
    height: 297px;
    border-radius: 18px;
    overflow: hidden;
    background: linear-gradient(160deg, var(--card) 0%, var(--card-deep) 100%);
  }
  .card--front { left: 60px; top: 170px; }
  .card--back  { left: 620px; top: 460px; }

  /* Front */
  .front-identity {
    position: absolute;
    inset: 0;
    display: flex;
    flex-direction: column;
    align-items: center;
    justify-content: center;
    gap: 18px;
  }
  .identity-dot {
    width: 70px;
    height: 70px;
    border-radius: 50%;
    background: var(--gold);
  }
  .front-name {
    color: var(--text-light);
    font-weight: 600;
    font-size: 40px;
    letter-spacing: 1px;
    text-transform: uppercase;
  }

  /* Back */
  .back-art {
    position: absolute;
    inset: 0;
    width: 520px;
    height: 297px;
  }
  .back-identity {
    position: absolute;
    left: 320px;
    top: 60px;
    width: 190px;
    display: flex;
    flex-direction: column;
    align-items: center;
    gap: 14px;
  }
  .back-identity .identity-dot {
    width: 64px;
    height: 64px;
  }
  .back-name {
    color: var(--ink);
    font-weight: 600;
    font-size: 22px;
    letter-spacing: 0.5px;
    text-transform: uppercase;
  }
  .contact {
    position: absolute;
    left: 44px;
    top: 128px;
    color: var(--text-light);
    font-size: 13.5px;
    line-height: 1.3;
  }
  .contact__name {
    color: var(--gold);
    font-weight: 600;
    font-size: 19px;
    text-transform: uppercase;
    letter-spacing: 0.3px;
  }
  .contact__title {
    font-size: 15px;
    margin-bottom: 14px;
  }
  .contact__address { margin-bottom: 14px; }
  .contact__list { list-style: none; }
  .contact__list li {
    display: flex;
    align-items: center;
    gap: 8px;
  }
  .contact__icon {
    width: 11px;
    height: 11px;
    flex: none;
  }
</style>
</head>
<body>

  <section class="card card--front" aria-label="Card front">
    <div class="front-identity">
      <span class="identity-dot"></span>
      <span class="front-name">Velmont Arc</span>
    </div>
  </section>

  <section class="card card--back" aria-label="Card back">
    <svg class="back-art" viewBox="0 0 520 297" aria-hidden="true">
      <circle cx="410" cy="122" r="185" fill="var(--paper)"/>
      <path d="M403.6 280.4 A165 165 0 0 1 263 59.6" fill="none" stroke="var(--gold)" stroke-width="5" stroke-linecap="round"/>
    </svg>

    <div class="back-identity">
      <span class="identity-dot"></span>
      <span class="back-name">Velmont Arc</span>
    </div>

    <div class="contact">
      <p class="contact__name">Dorian Kessler</p>
      <p class="contact__title">President</p>
      <p class="contact__address">2206 Larkfield Street<br>Brookhaven, MO 63190</p>
      <ul class="contact__list">
        <li>
          <svg class="contact__icon" viewBox="0 0 12 12"><path d="M2.5 1 L4.5 1 L5.2 3.6 L3.9 4.6 Q5 7 7.4 8.1 L8.4 6.8 L11 7.5 L11 9.5 Q10.5 11 9 11 Q1 10 1 3 Q1 1.5 2.5 1 Z" fill="var(--gold)"/></svg>
          <span>469-555-0172</span>
        </li>
        <li>
          <svg class="contact__icon" viewBox="0 0 12 12"><rect x="1" y="2.5" width="10" height="7" fill="none" stroke="var(--gold)" stroke-width="1.2"/><path d="M1 2.5 L6 6.5 L11 2.5" fill="none" stroke="var(--gold)" stroke-width="1.2"/></svg>
          <span>info@velmontarc.com</span>
        </li>
        <li>
          <svg class="contact__icon" viewBox="0 0 12 12"><circle cx="6" cy="6" r="5" fill="none" stroke="var(--gold)" stroke-width="1.1"/><ellipse cx="6" cy="6" rx="2.2" ry="5" fill="none" stroke="var(--gold)" stroke-width="1"/><path d="M1 6 H11" stroke="var(--gold)" stroke-width="1"/></svg>
          <span>www.velmontarc.com</span>
        </li>
      </ul>
    </div>
  </section>

</body>
</html>
```